U.S. Popcorn company needs business cards

We are a popcorn company that manufactures popcorn and sells it to grocery stores worldwide. Our theme is "Americana" and our logo is U.S. route 66 which is the most famous highway in the U.S.

We would like the design to be simple and to use both sides. On the back side we would like to see just the logo and website. The front would be normal details

Target Market(s)

Wholesalers, grocers and distributors

Industry/Entity Type

Manufacture

Contact Information for Business Card

Business name: Prairie Lantern Popcorn
Phone: +1 555 308 4726
Email: Dale@prairielanternpopcorn.com
website: www.prairielanternpopcorn.com
Tag Line: "Fresh from the fields"
Name: Dale Whitcombe
Title: Founder/President

Requirements
Must have
• Either this design should be fun or clean and simple. I will let you show me your thougths.
Nice to have
• Anything that ties in the real Hwy Route 66.
• Colors might need to be red, white and blue incorporated.
Should not have
• Not be too busy.

```html
<!DOCTYPE html>
<html lang="en">
<head>
<meta charset="utf-8">
<title>Prairie Lantern Popcorn – Business Card</title>
<link rel="stylesheet" href="https://fonts.googleapis.com/css2?family=Source+Sans+3:wght@400;600;700&display=swap">
<style>
  :root {
    --backdrop: #141414;
    --card-white: #ffffff;
    --brand-red: #e41e26;
    --ink: #231f20;
    --brand-blue: #1c2f7a;
  }
  * { margin: 0; padding: 0; box-sizing: border-box; }
  html, body {
    width: 1200px;
    height: 900px;
    overflow: hidden;
    background: var(--backdrop);
    font-family: "Source Sans 3", "Myriad Pro", Arial, sans-serif;
  }
  .stage { position: relative; width: 1200px; height: 900px; }
  .card {
    position: absolute;
    top: 306px;
    width: 440px;
    height: 271px;
    border-radius: 10px;
    overflow: hidden;
  }
  .card--front { left: 149px; background: var(--card-white); }
  .card--back { left: 608px; background: var(--brand-red); }

  .brand-name {
    position: absolute;
    font-weight: 700;
    text-align: center;
    line-height: 1.05;
    text-transform: uppercase;
  }
  .card--front .brand-name {
    left: 30px; top: 84px; width: 154px;
    font-size: 24px; color: var(--brand-red);
  }
  .card--back .brand-name {
    left: 145px; top: 84px; width: 150px;
    font-size: 24px; color: var(--card-white);
  }
  .brand-dot {
    position: absolute;
    width: 12px; height: 12px; border-radius: 50%;
  }
  .card--front .brand-dot { left: 101px; top: 64px; background: var(--brand-blue); }
  .card--back .brand-dot { left: 214px; top: 64px; background: var(--card-white); }

  .person { position: absolute; left: 209px; top: 44px; }
  .person__name {
    font-size: 15.5px; font-weight: 700; color: var(--brand-red);
    text-transform: uppercase; line-height: 1.1;
  }
  .person__title { font-size: 12.5px; color: var(--ink); line-height: 1.3; }

  .contact { position: absolute; left: 209px; top: 141px; list-style: none; }
  .contact__item {
    display: flex; align-items: center; gap: 7px;
    font-size: 12.5px; color: var(--ink); height: 16px;
  }
  .contact__icon { width: 9px; height: 9px; fill: var(--brand-red); flex: none; }

  .tagline {
    position: absolute; left: 209px; top: 201px;
    font-size: 15.5px; font-weight: 600; color: var(--brand-red);
    letter-spacing: 0.8px; text-transform: uppercase;
  }

  .back-pattern {
    position: absolute; inset: 0;
    background: linear-gradient(180deg, #e21d25, #dc1b23);
  }
  .back-site {
    position: absolute; left: 0; right: 0; top: 229px;
    text-align: center; font-size: 12.5px; font-weight: 600; color: var(--card-white);
  }
</style>
</head>
<body>
<main class="stage">
  <section class="card card--front" aria-label="Business card front">
    <span class="brand-dot"></span>
    <p class="brand-name">Prairie Lantern Popcorn</p>

    <div class="person">
      <h1 class="person__name">Dale Whitcombe</h1>
      <p class="person__title">Founder/President</p>
    </div>

    <ul class="contact">
      <li class="contact__item">
        <svg class="contact__icon" viewBox="0 0 10 10" aria-hidden="true"><path d="M1 3c0-1 1-1.5 4-1.5S9 2 9 3v1H7V3H3v1H1z"/><rect x="2" y="5" width="6" height="4" rx="1"/></svg>
        +1 555 308 4726
      </li>
      <li class="contact__item">
        <svg class="contact__icon" viewBox="0 0 10 10" aria-hidden="true"><path d="M0 2h10v1L5 6 0 3z"/><path d="M0 4l5 3 5-3v4H0z"/></svg>
        Dale@prairielanternpopcorn.com
      </li>
      <li class="contact__item">
        <svg class="contact__icon" viewBox="0 0 10 10" aria-hidden="true"><circle cx="5" cy="5" r="4.5"/></svg>
        www.prairielanternpopcorn.com
      </li>
    </ul>

    <p class="tagline">Fresh from the fields</p>
  </section>

  <section class="card card--back" aria-label="Business card back">
    <div class="back-pattern" role="img" aria-label="Faint repeating brand pattern on red"></div>
    <span class="brand-dot"></span>
    <p class="brand-name">Prairie Lantern Popcorn</p>
    <p class="back-site">www.prairielanternpopcorn.com</p>
  </section>
</main>
</body>
</html>
```